Business Card (double-sided) and Stationary Design for dental office

1) Business Card Design: We need a business card design for a dental specialty office.
Texts should contain:
The name of our office "Brindle Oaks Orthodontics"
Tagline: "Specialist in Orthodontic and Maxillofacial Orthopedics"
Tag line: "Creating "Tolvering" smiles for Children and Adults"
Doctor name: "Doctor Name"
Office Address:
"123 Street Name
City, State Zip code"
Office email address: office@brindleoaksortho.com
Website: www.brindleoaksortho.com

We will provide the full office address once the design is selected
Theme: beach, paradise, coastal, wave
We would like to have some creativity in design. Some acceptable ideas: front page: logo and office name. Back page: more detail information, and map to office in form of an island. Please see sample from our other location, but you DON'T HAVE TO USE OR COPY THE SAME CONCEPT.

IF POSSIBLE, PLEASE SUBMIT AT LEAST TWO CONCEPTS: ONE WITH THE BACK LOOKING SIMILAR TO WHAT IS IN THE SAMPLE, AND ONE DIFFERENT.

Color: designer to choose. We have different shade of blues and sand color in our office. Please see logo.

2) Please also design a matching set of stationary that compliment the business card and our logo.

Target Market(s)

Dental

Contact Information for Business Card

See descriptions

Font styles to use
Other font styles liked:
• Matching texts in logo

Colors
0054AA
0677BA
7BADD7
CADEEF
E8F1F8
0094D4
00A9DD
6FCCEA
C7EBF8
E9F6FB
00AB8E
00BBA5
67D7C9
C6EFE9
E9F9F6

Requirements
Must have
• Double-sided
Nice to have
• Beach coastal theme
Should not have
• Any shape or drawing of of tooth or teeth. We don’t need these. You don't necessarily have to just cut and paste the logo art and text as a whole, you have the liberty to rearrange the text.

```html
<!DOCTYPE html>
<html lang="en">
<head>
<meta charset="utf-8">
<title>Brindle Oaks Orthodontics – Business Card</title>
<link href="https://fonts.googleapis.com/css2?family=Raleway:wght@400;500;600;700&family=Arimo:wght@400&display=swap" rel="stylesheet">
<style>
  :root {
    --stage: #141415;
    --card-dark: #2a2a2c;
    --card-light: #ffffff;
    --edge: #2f8aa6;
    --teal-deep: #2f8cab;
    --teal-mid: #3fa3b3;
    --mint: #74d0bf;
    --text-light: #e4e4e4;
    --text-soft: #d6d6d6;
    --rule-dark: #8a8a8a;
    --rule-light: #c9c9c9;
    --ghost: #efefef;
    --note: #555555;
  }
  * { box-sizing: border-box; margin: 0; padding: 0; }
  html, body { width: 1200px; height: 820px; overflow: hidden; }
  body {
    background: var(--stage);
    font-family: "Raleway", sans-serif;
    position: relative;
  }
  .card {
    position: absolute;
    top: 250px;
    width: 540px;
    height: 310px;
    overflow: hidden;
  }

  /* Front */
  .card-front {
    left: 40px;
    background: var(--card-dark);
    border-left: 3px solid var(--edge);
    border-bottom: 3px solid var(--edge);
  }
  .brand {
    position: absolute;
    top: 34px;
    left: 168px;
    display: flex;
    align-items: center;
    gap: 14px;
  }
  .brand-dot {
    width: 68px; height: 68px;
    border-radius: 50%;
    background: var(--teal-deep);
    flex: none;
  }
  .brand-name {
    font-weight: 600;
    font-size: 24px;
    color: var(--mint);
    line-height: 1.15;
    letter-spacing: 0.3px;
  }
  .divider {
    position: absolute;
    top: 120px;
    left: 60px;
    width: 440px;
    height: 1px;
    background: var(--rule-dark);
  }
  .person {
    position: absolute;
    top: 130px;
    left: 26px;
    color: var(--text-light);
  }
  .person-name {
    font-weight: 700;
    font-size: 22px;
    line-height: 26px;
    color: var(--teal-mid);
  }
  .person-name .last { color: var(--mint); }
  .person-role { font-size: 14px; line-height: 18px; margin-top: 2px; }
  .address {
    font-family: "Arimo", sans-serif;
    font-size: 13px;
    line-height: 18px;
    margin-top: 10px;
    padding-left: 14px;
    color: var(--text-soft);
  }
  .contact {
    position: absolute;
    top: 134px;
    right: 22px;
    font-family: "Arimo", sans-serif;
    font-size: 13px;
    line-height: 20px;
    color: var(--text-light);
    text-align: right;
  }
  .contact-row { display: flex; align-items: center; justify-content: flex-end; gap: 6px; }
  .contact-row svg { width: 13px; height: 13px; flex: none; }
  .taglines {
    position: absolute;
    left: 60px;
    bottom: 16px;
    font-weight: 500;
    font-size: 15px;
    line-height: 22px;
  }
  .tagline-primary { color: var(--teal-deep); }
  .tagline-secondary { color: var(--mint); padding-left: 24px; font-weight: 600; }

  /* Back */
  .card-back {
    left: 620px;
    background: var(--card-light);
    border-left: 3px solid var(--edge);
    border-bottom: 3px solid var(--edge);
  }
  .back-mark {
    position: absolute;
    top: 30px;
    left: 250px;
    width: 250px; height: 250px;
    border-radius: 50%;
    background: var(--ghost);
  }
  .appt-title {
    position: absolute;
    top: 58px;
    left: 150px;
    font-weight: 500;
    font-size: 26px;
    color: var(--teal-deep);
  }
  .appt-line {
    position: absolute;
    left: 120px;
    width: 330px;
    height: 1px;
    background: var(--rule-light);
  }
  .appt-line.first { top: 140px; }
  .appt-line.second { top: 185px; left: 150px; }
  .appt-note {
    position: absolute;
    bottom: 38px;
    left: 0; right: 0;
    text-align: center;
    font-family: "Arimo", sans-serif;
    font-size: 11.5px;
    color: var(--note);
  }
</style>
</head>
<body>

  <section class="card card-front" aria-label="Business card front">
    <div class="brand">
      <span class="brand-dot"></span>
      <span class="brand-name">Brindle Oaks<br>Orthodontics</span>
    </div>

    <div class="divider"></div>

    <div class="person">
      <p class="person-name">Marcus <span class="last">Hale</span></p>
      <p class="person-role">Managing Director</p>
      <p class="address">123 Street Name<br>City, State Zip code</p>
    </div>

    <div class="contact">
      <p class="contact-row">office@brindleoaksortho.com
        <svg viewBox="0 0 16 16" aria-hidden="true"><rect x="1" y="3" width="14" height="10" fill="none" stroke="#3fa3b3" stroke-width="1.6"/><path d="M1 3l7 6 7-6" fill="none" stroke="#3fa3b3" stroke-width="1.6"/></svg>
      </p>
      <p class="contact-row">www.brindleoaksortho.com
        <svg viewBox="0 0 16 16" aria-hidden="true"><circle cx="8" cy="8" r="6.5" fill="none" stroke="#3fa3b3" stroke-width="1.4"/><ellipse cx="8" cy="8" rx="3" ry="6.5" fill="none" stroke="#3fa3b3" stroke-width="1.2"/><path d="M1.5 8h13" stroke="#3fa3b3" stroke-width="1.2"/></svg>
      </p>
    </div>

    <div class="taglines">
      <p class="tagline-primary">Specialist in Orthodontic and Maxillofacial Orthopedics</p>
      <p class="tagline-secondary">Creating Tolvering smiles for Children and Adults</p>
    </div>
  </section>

  <section class="card card-back" aria-label="Appointment card back">
    <div class="back-mark"></div>
    <h2 class="appt-title">Next Appointment</h2>
    <div class="appt-line first"></div>
    <div class="appt-line second"></div>
    <p class="appt-note">If you unable to keep appointment, please give 24 hours notice</p>
  </section>

</body>
</html>
```